BRN website video quote promotion tiles

We are promoting vehicle leasing by video, which contains several quotation examples imported from the video. We must re-vamp the quotation tiles, contact boxes, and contact form. The first tile is generated from the video, so this must be a separate project. We are looking for a welcoming, professional flow and leave color choices to design with an emphasis on communication prompts, and additional prompts in the design would be welcome.

Target Market(s)

Any Customer interaction from the tile quotes, contact, call, message,

Industry/Entity Type

vehicle leasing

Coding

Coded - Design and coding required

Number of Pages Required

1 page

Colors

Designer to choose colors to be used in the design.

Requirements
Must have
• emphasis on point of contact and visual impact on quote tile excluding main one
Should not have
• changes to the quote structure as these imported from video pricing no changes to main image as this template which can addressed as separate project

```html
<!DOCTYPE html>
<html lang="en">
<head>
<meta charset="utf-8">
<title>Vehicle Leasing Contact Form and Quote Tiles</title>
<link href="https://fonts.googleapis.com/css2?family=Poppins:wght@400;500;600;700&display=swap" rel="stylesheet">
<style>
:root{
  --bg-grey:#e9e9e9;
  --white:#ffffff;
  --ink:#111111;
  --green:#73b62a;
  --green-btn:#4cbb47;
  --green-light:#7dd36e;
  --orange:#d86a27;
  --orange-light:#e9974f;
  --yellow:#eabd41;
  --red:#e01b1b;
  --line:#bdbdbd;
}
*{margin:0;padding:0;box-sizing:border-box}
html,body{width:1200px;height:1069px;overflow:hidden;background:var(--white);font-family:'Poppins',sans-serif;color:var(--ink)}
.page{position:relative;width:1200px;height:1069px}
.contact-section{position:absolute;left:0;top:0;width:1200px;height:655px;background:var(--bg-grey)}
.accent{position:absolute;border:8px solid var(--green);border-radius:10px}
.accent-top{left:234px;top:113px;width:126px;height:125px;border-right:none;border-bottom:none}
.accent-bottom{left:856px;top:438px;width:125px;height:125px;border-left:none;border-top:none}
.contact-card{position:absolute;left:241px;top:121px;width:735px;height:437px;background:var(--white);border-radius:8px 50px 8px 50px}
.contact-title{position:absolute;left:0;top:35px;width:100%;text-align:center;font-size:26px;font-weight:600;padding-left:26px}
.title-rule{position:absolute;left:331px;top:80px;width:67px;height:2px;background:var(--green)}
.field{position:absolute;width:301px;height:45px;border:1px solid var(--line);border-radius:23px;font-size:13px;padding:0 0 0 23px;display:flex;align-items:center;color:#222}
.field-message{width:616px;height:97px;border-radius:8px;align-items:flex-start;padding:14px 0 0 26px}
.submit-btn{position:absolute;left:276px;top:328px;width:179px;height:49px;background:var(--orange);color:var(--white);border-radius:25px;font-size:15px;font-weight:700;display:flex;align-items:center;justify-content:center}
.quote-tile{position:absolute;overflow:hidden}
.tile-outline{left:99px;top:745px;width:330px;height:179px;border:1.5px solid var(--yellow);border-radius:38px 0 50px 0;background:var(--white)}
.tile-filled{left:446px;top:741px;width:321px;height:179px;background:var(--orange);border-radius:6px}
.tile-bar{left:789px;top:741px;width:330px;height:180px;border:1px solid #cfcfcf;background:var(--white)}
.price-disc{position:absolute;border-radius:50%;background:var(--yellow)}
.price{position:absolute;transform:translate(-50%,-50%);color:var(--white);font-weight:700;font-size:22px;white-space:nowrap}
.vat-pill{position:absolute;background:var(--white);color:var(--green-btn);font-size:9px;border-radius:8px;display:flex;align-items:center;justify-content:center;letter-spacing:.3px}
.tile-heading{position:absolute;font-weight:700;font-size:20px;white-space:nowrap;transform:translateY(-50%)}
.tile-text{position:absolute;font-size:13px;font-weight:500;white-space:nowrap;transform:translateY(-50%)}
.not-maint{position:absolute;font-size:11px;font-weight:500;color:var(--red);transform:translateY(-50%)}
.cta{position:absolute;display:flex;align-items:center;justify-content:center;gap:4px;color:var(--white);font-weight:600;font-size:13px}
.cta svg{width:15px;height:15px}
.cta-call{background:linear-gradient(90deg,var(--orange-light),var(--orange))}
.cta-msg{background:linear-gradient(90deg,var(--green-light),var(--green-btn))}
.msg-dot{width:14px;height:14px;border-radius:50%;background:var(--white)}
.list-row{position:absolute;display:flex;align-items:center;gap:3px;font-size:12px;font-weight:500;color:var(--white);white-space:nowrap;transform:translateY(-50%)}
.list-row svg{width:8px;height:8px}
.sq-row{position:absolute;display:flex;align-items:center;gap:9px;font-size:13px;font-weight:500;white-space:nowrap;transform:translateY(-50%)}
.sq{width:4px;height:4px;background:var(--yellow)}
</style>
</head>
<body>
<div class="page">
  <section class="contact-section">
    <div class="accent accent-top"></div>
    <div class="accent accent-bottom"></div>
    <form class="contact-card">
      <h2 class="contact-title">Please submit your contact details</h2>
      <div class="title-rule"></div>
      <div class="field" style="left:59px;top:103px">First Name</div>
      <div class="field" style="left:375px;top:103px">Last Name</div>
      <div class="field" style="left:59px;top:160px">Email address</div>
      <div class="field" style="left:374px;top:160px">Phone Number</div>
      <div class="field field-message" style="left:58px;top:218px">Your Message</div>
      <div class="submit-btn">SUBMIT NOW</div>
    </form>
  </section>

  <svg width="0" height="0" style="position:absolute">
    <defs>
      <symbol id="phone-icon" viewBox="0 0 24 24"><path fill="#fff" d="M6.6 10.8a15.1 15.1 0 0 0 6.6 6.6l2.2-2.2c.3-.3.7-.4 1-.2 1.1.4 2.3.6 3.6.6.6 0 1 .4 1 1V20c0 .6-.4 1-1 1A17 17 0 0 1 3 4c0-.6.4-1 1-1h3.5c.6 0 1 .4 1 1 0 1.3.2 2.5.6 3.6.1.3 0 .7-.2 1z"/></symbol>
      <symbol id="chevron-icon" viewBox="0 0 10 10"><path d="M3 1.5 6.5 5 3 8.5" fill="none" stroke="#fff" stroke-width="2" stroke-linecap="round" stroke-linejoin="round"/></symbol>
    </defs>
  </svg>

  <article class="quote-tile tile-outline">
    <div class="price-disc" style="left:236px;top:-41px;width:124px;height:124px"></div>
    <div class="price" style="left:284px;top:25px">£247.33</div>
    <div class="vat-pill" style="left:262px;top:44px;width:58px;height:15px">PLUSVAT</div>
    <div class="tile-heading" style="left:30px;top:42px;color:var(--orange)">CONTRACT HIRE</div>
    <div class="tile-text" style="left:30px;top:71px">3 years, 9+35, 10K miles annually</div>
    <div class="not-maint" style="left:32px;top:89px">Not Maintained</div>
    <div class="cta cta-call" style="left:33px;top:122px;width:132px;height:34px"><svg><use href="#phone-icon"/></svg>Contact us</div>
    <div class="cta cta-msg" style="left:172px;top:122px;width:131px;height:34px"><span class="msg-dot"></span>Message us</div>
  </article>

  <article class="quote-tile tile-filled">
    <div class="price-disc" style="left:209px;top:11px;width:98px;height:98px"></div>
    <div class="price" style="left:258px;top:50px">£247.33</div>
    <div class="vat-pill" style="left:232px;top:69px;width:57px;height:15px">PLUSVAT</div>
    <div class="tile-heading" style="left:25px;top:29px;color:var(--white)">CONTRACT HIRE</div>
    <div class="list-row" style="left:28px;top:54px"><svg><use href="#chevron-icon"/></svg>3 years</div>
    <div class="list-row" style="left:28px;top:71px"><svg><use href="#chevron-icon"/></svg>9+35</div>
    <div class="list-row" style="left:28px;top:88px"><svg><use href="#chevron-icon"/></svg>10K miles annually</div>
    <div class="not-maint" style="left:31px;top:113px;color:var(--white)">Not Maintained</div>
    <div class="cta" style="left:28px;top:130px;width:130px;height:33px;border:1.5px solid var(--white);border-radius:17px"><svg><use href="#phone-icon"/></svg>Contact us</div>
    <div class="cta cta-msg" style="left:165px;top:130px;width:131px;height:33px;border-radius:17px"><span class="msg-dot"></span>Message us</div>
  </article>

  <article class="quote-tile tile-bar">
    <div class="price-disc" style="left:220px;top:-35px;width:200px;height:200px"></div>
    <div class="price" style="left:282px;top:26px">£247.33</div>
    <div class="vat-pill" style="left:263px;top:44px;width:56px;height:14px">PLUSVAT</div>
    <div class="tile-heading" style="left:27px;top:37px;font-size:21px">Contract Hire</div>
    <div class="sq-row" style="left:29px;top:66px"><span class="sq"></span>3 years</div>
    <div class="sq-row" style="left:29px;top:83px"><span class="sq"></span>9+35</div>
    <div class="sq-row" style="left:29px;top:100px"><span class="sq"></span>10K miles annually</div>
    <div class="not-maint" style="left:28px;top:122px">Not Maintained</div>
    <div class="cta cta-call" style="left:0;top:143px;width:164px;height:37px"><svg><use href="#phone-icon"/></svg>Contact us</div>
    <div class="cta cta-msg" style="left:164px;top:143px;width:166px;height:37px"><span class="msg-dot"></span>Message us</div>
  </article>
</div>
</body>
</html>
```